Stonebrace Business Card Design

The Stonebrace Co is an aggregate (crushing) equipment dealer serving Western Canadian provinces. Stonebrace is a distributor of aggregate equipment for different manufacturers.

We are looking to change and update the existing business card which has been used since the existence of the company. A copy of existing card has been attached for reference. The Stonebrace Co logo we want to remain the same and we want the green color to remain the same.

We are wanting something new with a different look. A refreshing card to show a new modern and updated look. No longer wanting to have the manufacturers on the back of the card but something more like our logo on the back of the card with a statement like "Crushing Solutions"

ideas could be:
- card can be different colors on front and back
- front or reverse of the card could possibly be the green color with the logo in black

Target Market(s)

Owners of Aggregate/Crushing companies

Contact Information for Business Card

see above

Requirements
Must have
• - logo to remain same along with same font within logo
• - green color to remain same
Nice to have
• as noted above under project description
Should not have

```html
<!DOCTYPE html>
<html lang="en">
<head>
<meta charset="utf-8">
<title>The Stonebrace Co – Business Card</title>
<link rel="stylesheet" href="https://fonts.googleapis.com/css2?family=Raleway:wght@400;500;800&family=Open+Sans:wght@400&display=swap">
<style>
  :root {
    --brand-green: #8b8a33;
    --ink: #231f20;
    --paper: #ffffff;
    --backdrop: #d9d9d7;
    --text-dark: #1f1f1f;
  }
  * { margin: 0; padding: 0; box-sizing: border-box; }
  html, body { width: 1200px; height: 1000px; overflow: hidden; background: var(--backdrop); }
  .stage { position: relative; width: 1200px; height: 1000px; }

  .card {
    position: absolute;
    background: var(--paper);
    border-radius: 32px;
    overflow: hidden;
    box-shadow: 0 14px 28px rgba(0,0,0,.22);
  }

  /* Front */
  .card--front { left: 150px; top: 102px; width: 633px; height: 360px; }
  .front-brand {
    position: absolute; left: 0; right: 0; top: 150px;
    display: flex; align-items: center; justify-content: center; gap: 16px;
  }
  .brand-dot { width: 26px; height: 26px; border-radius: 50%; background: var(--brand-green); }
  .front-brand .brand-name {
    font-family: 'Raleway', sans-serif; font-weight: 800;
    font-size: 34px; color: var(--ink); letter-spacing: .5px;
  }
  .front-tab { position: absolute; left: 0; top: 0; width: 633px; height: 360px; }
  .front-tagline {
    position: absolute; left: 362px; top: 307px;
    font-family: 'Raleway', sans-serif; font-weight: 400;
    font-size: 19px; color: var(--paper); letter-spacing: .3px;
  }

  /* Back */
  .card--back { left: 368px; top: 546px; width: 640px; height: 364px; }
  .back-header {
    position: absolute; left: 0; top: 0; width: 100%; height: 132px;
    background: var(--brand-green);
  }
  .holder-name {
    position: absolute; left: 31px; top: 78px;
    font-family: 'Raleway', sans-serif; font-weight: 500;
    font-size: 29px; color: var(--paper); letter-spacing: .3px;
  }
  .back-header .brand-name {
    position: absolute; right: 52px; top: 93px;
    font-family: 'Raleway', sans-serif; font-weight: 800;
    font-size: 15px; color: var(--paper);
  }
  .address-band {
    position: absolute; left: 100px; top: 132px; width: 438px; height: 30px;
    background: var(--ink); border-radius: 0 0 24px 24px;
    font-family: 'Open Sans', sans-serif; font-size: 14px; color: var(--paper);
    display: flex; align-items: center; justify-content: center; letter-spacing: .2px;
  }
  .contact-list { position: absolute; list-style: none; }
  .contact-list--phones { left: 28px; top: 184px; }
  .contact-list--web { left: 320px; top: 184px; }
  .contact-list li {
    display: flex; align-items: center; height: 35px;
    font-family: 'Open Sans', sans-serif; font-size: 23px; color: var(--text-dark);
  }
  .contact-list svg { width: 20px; height: 20px; margin-right: 17px; fill: var(--ink); flex: none; }
  .contact-list--web svg { margin-right: 14px; }
  .back-footer {
    position: absolute; left: 0; bottom: 0; width: 100%; height: 68px;
    background: var(--ink);
    display: flex; align-items: center; justify-content: center;
    font-family: 'Raleway', sans-serif; font-size: 20px; color: var(--paper);
  }
  .back-footer span { padding: 0 12px; }
  .back-footer span + span { border-left: 2px solid var(--paper); line-height: 28px; }
</style>
</head>
<body>
<main class="stage">

  <section class="card card--front" aria-label="Business card front">
    <div class="front-brand">
      <span class="brand-dot"></span>
      <span class="brand-name">THE STONEBRACE CO.</span>
    </div>
    <svg class="front-tab" viewBox="0 0 633 360" aria-hidden="true">
      <path d="M338 288 H633 V360 H308 L326 300 Q330 288 338 288 Z" fill="var(--brand-green)"/>
    </svg>
    <p class="front-tagline">CRUSHING SOLUTIONS</p>
  </section>

  <section class="card card--back" aria-label="Business card back">
    <header class="back-header">
      <h1 class="holder-name">DEREK HOLLAND</h1>
      <span class="brand-name">THE STONEBRACE CO.</span>
    </header>
    <p class="address-band">2218-48B AVENUE, NISKU, ALBERTA T9E 7R2</p>

    <ul class="contact-list contact-list--phones">
      <li>
        <svg viewBox="0 0 24 24" aria-label="Office"><path d="M2 8c2-4 18-4 20 0v2h-5V8H7v2H2z"/><path d="M6 11h12l3 9H3z M10 14a2 2 0 1 0 4 0a2 2 0 1 0-4 0z"/></svg>
        780 . 555 . 0142
      </li>
      <li>
        <svg viewBox="0 0 24 24" aria-label="Mobile"><path d="M6.6 10.8a15 15 0 0 0 6.6 6.6l2.2-2.2a1 1 0 0 1 1-.25 11.4 11.4 0 0 0 3.6.6 1 1 0 0 1 1 1V20a1 1 0 0 1-1 1A17 17 0 0 1 3 4a1 1 0 0 1 1-1h3.5a1 1 0 0 1 1 1c0 1.25.2 2.45.6 3.6a1 1 0 0 1-.25 1z"/></svg>
        780 . 555 . 0186
      </li>
      <li>
        <svg viewBox="0 0 24 24" aria-label="Fax"><path d="M7 3h10v5H7z"/><path d="M4 9h16a2 2 0 0 1 2 2v6h-4v4H6v-4H2v-6a2 2 0 0 1 2-2zm4 6v4h8v-4z"/></svg>
        780 . 555 . 0193
      </li>
    </ul>

    <ul class="contact-list contact-list--web">
      <li>
        <svg viewBox="0 0 24 24" aria-label="Email"><path d="M3 6h18v2l-9 5.5L3 8z"/><path d="M3 10l9 5.5L21 10v8H3z"/></svg>
        derek@stonebr.com
      </li>
      <li>
        <svg viewBox="0 0 24 24" aria-label="Website"><path d="M12 2a10 10 0 1 0 0 20a10 10 0 1 0 0-20zm0 2c.9 0 2.2 2 2.7 5H9.3C9.8 6 11.1 4 12 4zM4.3 9h3c-.1.9-.1 2-.1 3s0 2.1.1 3h-3a8 8 0 0 1 0-6zm5 0h5.4c.1.9.1 2 .1 3s0 2.1-.1 3H9.3c-.1-.9-.1-2-.1-3s0-2.1.1-3zm7.4 0h3a8 8 0 0 1 0 6h-3c.1-.9.1-2 .1-3s0-2.1-.1-3zM9.3 17h5.4c-.5 3-1.8 5-2.7 5s-2.2-2-2.7-5z"/></svg>
        www.stonebrace.ca
      </li>
    </ul>

    <footer class="back-footer">
      <span>SCREENERS</span><span>CRUSHERS</span><span>STACKERS</span>
    </footer>
  </section>

</main>
</body>
</html>
```